Industry / Entity Type

Financial consultancy / advisers

Current site is: http://www.brightmoor-counsel.com

Looking for a complete overhaul of this site, we are after a clean modern look. Will require the ability to easily add, update and remove content, hence the WordPress design.
Example:
Add case studies
Industry documentation (downloadable brochures / flyers and such)

What we like from our current site is the colour the fonts and the logo (the city of London) we would like to have other city outlines (NYC and Tokyo, Hong Kong, Singapore).

The site will be used by our potential clients to get in contact and re-view the case studies, if possible would like to have a client login area where they can download our documents like NDA’s etc and T&C’s.

Task Outline

Create a Web Design (Coded - Design and coding required)
Designer must provide full implementation/coding depending on the platform chosen by the client (i.e. WordPress theme, HTML/CSS, bootstrap etc.)

Task Description

I need a full website built that must work on desktop and mobile. I can provide the London city skyline and the font file, which we have used. Some stock industrial photos will be required.

Requirements:

*Splash page
*What We Do
*How We do it
*Who Are We? To have the same information and links as the current site
*Why use us?
*Clients: To have the same information and links as the current site
*Partners: To have the same information and links as the current site
*Contact:

Target Market(s)

Financial institutions trading Equities, Futures, Options, Forex and Fixed Income.
Regulators, Exchanges, ECN’s
Buy side firms and Sell side firms

Industry/Entity Type

Financial

Coding

Coded - Design and coding required

Number of Pages Required

5+ page

Font styles to use
Sans Serif

Colors
f04a50

Requirements
Must have
• Splash page
• What We Do
• How We do it
• Who Are We? To have the same information and links as the current site
• Why use us?
• Clients: To have the same information and links as the current site
• Partners: To have the same information and links as the current site
• Contact:

```html
<!DOCTYPE html>
<html lang="en">
<head>
<meta charset="utf-8">
<title>Brightmoor Counsel</title>
<link href="https://fonts.googleapis.com/css2?family=Roboto:ital,wght@0,300;0,400;0,500;0,700;1,400;1,500&family=Open+Sans:ital,wght@0,400;0,600;1,400&display=swap" rel="stylesheet">
<style>
:root{
  --brand:#f04a50;
  --brand-soft:#f0575c;
  --ink:#333333;
  --muted:#666666;
  --line:#e2e2e2;
  --panel:#f0f0f0;
  --footer:#1b1b1b;
  --footer-text:#d6d6d6;
  --white:#ffffff;
}
*{box-sizing:border-box;margin:0;padding:0}
html,body{width:1200px;height:3046px;overflow:hidden}
body{font-family:"Open Sans",Arial,sans-serif;color:var(--ink);background:var(--white);position:relative}
a{color:inherit;text-decoration:none}

/* header */
.site-header{position:absolute;top:0;left:0;width:1200px;height:118px;background:var(--white)}
.brand{position:absolute;left:100px;top:44px;display:flex;align-items:center;gap:12px}
.brand-mark{width:26px;height:26px;background:var(--brand)}
.brand-name{font-family:"Roboto",sans-serif;font-weight:400;font-size:24px;letter-spacing:2px;color:#444;text-transform:uppercase}
.top-contacts{position:absolute;right:100px;top:22px;display:flex;gap:34px;font-size:15px;color:#555}
.top-contacts span{display:flex;align-items:center;gap:12px}
.top-contacts .dot{width:26px;height:26px;border-radius:50%;background:var(--brand);display:flex;align-items:center;justify-content:center}
.main-nav{position:absolute;right:100px;top:78px;display:flex;gap:23px;font-family:"Roboto",sans-serif;font-size:13px;color:#444;text-transform:uppercase}
.main-nav a{padding-bottom:20px}
.main-nav a.active{color:var(--brand);border-bottom:3px solid var(--brand)}

/* hero */
.hero{position:absolute;top:118px;left:0;width:1200px;height:540px;background:linear-gradient(100deg,#3a3d42 0%,#6b6e72 40%,#9a9ea2 70%,#5d6166 100%)}
.hero-text{position:absolute;left:98px;top:192px;color:var(--white)}
.hero-title{font-family:"Roboto",sans-serif;font-weight:500;font-size:44px;line-height:46px;text-transform:uppercase}
.hero-title small{display:block;font-size:32px;line-height:40px}
.hero-lead{margin-top:14px;font-size:14px;font-weight:600;line-height:22px;width:370px}
.hero-dots{display:flex;gap:8px;margin-top:18px}
.hero-dots i{width:12px;height:12px;border-radius:50%;background:var(--white)}
.hero-dots i.on{box-shadow:0 0 0 3px rgba(255,255,255,.5);background:#ddd}

/* welcome band */
.welcome{position:absolute;top:658px;left:0;width:1200px;height:258px;background:linear-gradient(180deg,#f0575c 0%,#ef4f55 60%,#e94b51 100%);text-align:center;color:var(--white)}
.welcome h1{font-family:"Roboto",sans-serif;font-weight:500;font-size:32px;margin-top:48px;text-transform:uppercase}
.welcome p{width:880px;margin:20px auto 0;font-size:11px;line-height:21px}
.btn-outline{display:inline-block;border:1px solid var(--white);padding:8px 16px;font-family:"Roboto",sans-serif;font-size:13px;text-transform:uppercase;margin-top:20px}

/* services */
.services{position:absolute;top:916px;left:0;width:1200px;height:500px;text-align:center}
.section-title{font-family:"Roboto",sans-serif;font-weight:400;font-size:31px;color:#333;text-transform:uppercase}
.services .section-title{margin-top:74px}
.service-grid{position:absolute;top:172px;left:96px;width:1008px;display:flex;justify-content:space-between}
.service{width:240px}
.service-icon{width:106px;height:106px;border:2px solid var(--brand);border-radius:50%;margin:0 auto;display:flex;align-items:center;justify-content:center}
.service h3{font-family:"Roboto",sans-serif;font-weight:400;font-size:14px;margin-top:28px;text-transform:uppercase;color:#333}
.service p{font-size:11.5px;line-height:21px;color:#555;margin-top:10px}
.service .chev{margin-top:12px}

/* how we do it */
.how{position:absolute;top:1416px;left:0;width:1200px;height:436px;background:var(--panel)}
.how-media{position:absolute;left:0;top:0}
.how-text{position:absolute;left:680px;top:112px;width:420px}
.how-text h2{font-family:"Roboto",sans-serif;font-weight:400;font-size:31px;text-transform:uppercase;color:#333}
.how-text p{font-size:11.5px;line-height:21px;color:#555;margin-top:16px}
.how-text p + p{margin-top:12px}
.btn-brand-outline{display:inline-block;border:1px solid var(--brand);color:var(--brand);padding:7px 14px;font-family:"Roboto",sans-serif;font-size:12px;text-transform:uppercase;margin-top:16px}

/* blog */
.blog{position:absolute;top:1852px;left:0;width:1200px;height:584px;text-align:center}
.blog .section-title{margin-top:82px}
.title-rule{width:90px;height:1px;background:#ccc;margin:16px auto 0}
.blog-grid{position:absolute;top:174px;left:98px;width:1004px;display:flex;justify-content:space-between;text-align:left}
.post{width:314px}
.post-thumb{width:314px;height:164px;display:block}
.post h3{font-family:"Roboto",sans-serif;font-weight:400;font-size:16px;color:#444;margin-top:18px}
.post-meta{display:flex;gap:26px;font-family:"Roboto",sans-serif;font-style:italic;font-size:12px;color:#555;margin-top:12px;align-items:center}
.post-meta span{display:flex;align-items:center;gap:8px}
.post p{font-size:11.5px;line-height:20px;color:#555;margin-top:16px}

/* testimonial */
.testimonial{position:absolute;top:2436px;left:0;width:1200px;height:244px;background:#efefef}
.avatar{position:absolute;left:168px;top:50px;width:120px;height:120px;border-radius:50%;border:4px solid #fff;background:radial-gradient(circle at 50% 40%,#c9a48a,#7b6a5f 70%,#6a6a6a);box-shadow:0 0 0 1px #ddd}
.quote{position:absolute;left:313px;top:56px;width:740px;font-style:italic;font-size:13.5px;line-height:25px;color:#555}
.quote-author{position:absolute;left:313px;top:142px;font-family:"Roboto",sans-serif;font-style:italic;font-weight:500;font-size:15px;color:var(--brand)}
.quote-bars{position:absolute;left:313px;top:186px;display:flex;gap:4px}
.quote-bars i{width:24px;height:3px;background:#d8d8d8}
.quote-bars i.on{background:var(--brand)}

/* footer */
.site-footer{position:absolute;top:2680px;left:0;width:1200px;height:366px;background:var(--footer);color:var(--footer-text)}
.footer-col{position:absolute;top:48px}
.footer-col h4{font-family:"Roboto",sans-serif;font-weight:400;font-size:16px;color:#fff;text-transform:uppercase;margin-bottom:22px}
.contact-col{left:98px;width:260px}
.contact-row{display:flex;gap:16px;font-size:12.5px;line-height:22px;margin-bottom:14px}
.contact-row svg{flex:none;margin-top:3px}
.signup-col{left:408px;width:290px}
.signup-col p{font-size:11.5px;line-height:19px}
.field{margin-top:14px;width:286px;height:40px;background:#fff;color:#777;font-size:11px;padding:12px 14px}
.btn-brand{display:inline-block;margin-top:12px;background:var(--brand);color:#fff;font-family:"Roboto",sans-serif;font-weight:500;font-size:12px;padding:12px 14px;text-transform:uppercase}
.links-col{left:790px}
.links-col li{list-style:none;font-size:12px;line-height:24px}
.social-col{left:983px}
.social-col li{list-style:none;display:flex;align-items:center;gap:10px;font-size:13px;margin-bottom:12px}
.social-col li i{width:26px;height:26px;border:2px solid #ddd;border-radius:50%}
.copyright{position:absolute;top:318px;left:410px;font-size:12px;color:#ddd}
</style>
</head>
<body>

<header class="site-header">
  <a class="brand" href="#"><span class="brand-mark"></span><span class="brand-name">Brightmoor Counsel</span></a>
  <div class="top-contacts">
    <span><i class="dot"><svg width="12" height="12" viewBox="0 0 24 24"><path fill="#fff" d="M6.6 10.8a15 15 0 0 0 6.6 6.6l2.2-2.2c.3-.3.7-.4 1-.2 1.1.4 2.3.6 3.6.6.6 0 1 .4 1 1V20c0 .6-.4 1-1 1A17 17 0 0 1 3 4c0-.6.4-1 1-1h3.5c.6 0 1 .4 1 1 0 1.3.2 2.5.6 3.6.1.3 0 .7-.2 1z"/></svg></i>+44(0)20 7946 0321</span>
    <span><i class="dot"><svg width="12" height="12" viewBox="0 0 24 24"><path fill="#fff" d="M3 5h18v14H3z M3 5l9 7 9-7" stroke="#f04a50" stroke-width="1.5"/></svg></i>sales@brightmoor-counsel.com</span>
  </div>
  <nav class="main-nav">
    <a class="active" href="#">Home</a><a href="#">What we do</a><a href="#">How we do it</a><a href="#">Who are we</a><a href="#">Why use us</a><a href="#">Clients</a><a href="#">Partners</a><a href="#">Contact</a>
  </nav>
</header>

<section class="hero" role="img" aria-label="Photo of a business team meeting around a table in a bright office">
  <div class="hero-text">
    <h2 class="hero-title">Brightmoor<small>Counsel Advisers</small></h2>
    <p class="hero-lead">Sed ut perspiciatis unde omnis iste natus error sit voluptatem accusantium doloremque laudantium, totam</p>
    <div class="hero-dots"><i class="on"></i><i></i><i></i><i></i></div>
  </div>
</section>

<section class="welcome">
  <h1>Welcome to Brightmoor Counsel</h1>
  <p>Since founding Brightmoor Counsel in 2014 we have dedicated ourselves to the provision of services. What differentiates us from other advisers or consultancies is a genuine motivation to see our clients succeed. Today's technology allows our clients to take their knowledge to the market in ways that previous generations could only dream of. That's why Brightmoor is dedicated to seeing you choose the right technology strategy, ensuring you maintain a competitive edge over your peers.</p>
  <a class="btn-outline" href="#">Read more</a>
</section>

<section class="services">
  <h2 class="section-title">Our Services</h2>
  <div class="service-grid">
    <div class="service">
      <div class="service-icon"><svg width="40" height="32" viewBox="0 0 40 32" fill="none" stroke="#f04a50" stroke-width="2.5"><rect x="6" y="3" width="28" height="19" rx="1"/><path d="M1 27h38l-3 3H4z"/></svg></div>
      <h3>Product Development</h3>
      <p>Sed ut perspiciatis unde omnis iste natus error sit voluptatem accusantium doque laudantium, totam rem dolores</p>
      <svg class="chev" width="14" height="12" viewBox="0 0 14 12" fill="none" stroke="#f04a50" stroke-width="2"><path d="M2 1l5 4 5-4M2 6l5 4 5-4"/></svg>
    </div>
    <div class="service">
      <div class="service-icon"><svg width="44" height="34" viewBox="0 0 44 34" fill="#f04a50"><circle cx="22" cy="8" r="6"/><path d="M12 30c0-7 4-11 10-11s10 4 10 11z"/><circle cx="8" cy="12" r="4.5"/><path d="M0 30c0-6 3-9 8-9 2 0 3 .5 4 1-2 2-3 5-3 8z"/><circle cx="36" cy="12" r="4.5"/><path d="M44 30c0-6-3-9-8-9-2 0-3 .5-4 1 2 2 3 5 3 8z"/></svg></div>
      <h3>Interim Management</h3>
      <p>Sed ut perspiciatis unde omnis iste natus error sit voluptatem accusantium doque laudantium, totam rem dolores</p>
      <svg class="chev" width="14" height="12" viewBox="0 0 14 12" fill="none" stroke="#f04a50" stroke-width="2"><path d="M2 1l5 4 5-4M2 6l5 4 5-4"/></svg>
    </div>
    <div class="service">
      <div class="service-icon"><svg width="44" height="40" viewBox="0 0 44 40" fill="none" stroke="#f04a50" stroke-width="5"><circle cx="16" cy="22" r="7"/><path d="M16 8v4M16 32v4M2 22h4M26 22h4M6 12l3 3M23 29l3 3M6 32l3-3M23 15l3-3" stroke-width="4"/><circle cx="34" cy="10" r="4" stroke-width="3"/><path d="M34 2v3M34 15v3M26 10h3M39 10h3" stroke-width="3"/></svg></div>
      <h3>Process Outsourcing</h3>
      <p>Sed ut perspiciatis unde omnis iste natus error sit voluptatem accusantium doque laudantium, totam rem dolores</p>
      <svg class="chev" width="14" height="12" viewBox="0 0 14 12" fill="none" stroke="#f04a50" stroke-width="2"><path d="M2 1l5 4 5-4M2 6l5 4 5-4"/></svg>
    </div>
    <div class="service">
      <div class="service-icon"><svg width="40" height="40" viewBox="0 0 40 40" fill="none" stroke="#f04a50" stroke-width="4"><circle cx="16" cy="16" r="12"/><path d="M25 25l11 11M16 10v12M10 16h12" stroke-linecap="round"/></svg></div>
      <h3>Research</h3>
      <p>Sed ut perspiciatis unde omnis iste natus error sit voluptatem accusantium doque laudantium, totam rem dolores</p>
      <svg class="chev" width="14" height="12" viewBox="0 0 14 12" fill="none" stroke="#f04a50" stroke-width="2"><path d="M2 1l5 4 5-4M2 6l5 4 5-4"/></svg>
    </div>
  </div>
</section>

<section class="how">
  <svg class="how-media" width="650" height="436" viewBox="0 0 650 436" role="img" aria-label="Photo of a glowing light bulb on a dark sketched background">
    <defs>
      <radialGradient id="bulbGlow" cx="0.27" cy="0.35" r="0.6">
        <stop offset="0" stop-color="#c9a35a"/>
        <stop offset="0.35" stop-color="#5f6264"/>
        <stop offset="1" stop-color="#2f3436"/>
      </radialGradient>
    </defs>
    <polygon points="0,0 650,0 535,436 0,436" fill="url(#bulbGlow)"/>
  </svg>
  <div class="how-text">
    <h2>How We Do It</h2>
    <p>Lorem ipsum dolor sit amet, consectetur adipiscing elit, sed do eiusmod tempor incididunt ut labore et dolore magna aliqua. Ut enim ad minim veniam, quis nostrud exercitation ullamco laboris nisi ut aliquip ex ea</p>
    <p>Sed ut perspiciatis unde omnis iste natus error sit voluptatem accusantium doloremque laudantium, totam rem aperiam, eaque ipsa quae ab illo inventore veritatis et quasi architecto beatae vitae dicta sunt explicabo.</p>
    <a class="btn-brand-outline" href="#">Read more</a>
  </div>
</section>

<section class="blog">
  <h2 class="section-title">Latest Blog</h2>
  <div class="title-rule"></div>
  <div class="blog-grid">
    <article class="post">
      <svg class="post-thumb" viewBox="0 0 314 164" role="img" aria-label="Photo of colleagues in a meeting room"><rect width="314" height="164" fill="#7d858c"/></svg>
      <h3>Nemo enim ipsam voluptatem quia</h3>
      <div class="post-meta"><span><svg width="11" height="11" viewBox="0 0 12 12"><rect x="1" y="2" width="10" height="9" fill="none" stroke="#555" stroke-width="1.5"/><path d="M1 5h10" stroke="#555"/></svg>March 25, 2017</span><span><svg width="12" height="11" viewBox="0 0 12 11"><path d="M1 1h10v7H5l-3 2V8H1z" fill="none" stroke="#555" stroke-width="1.2"/></svg>No comments</span></div>
      <p>Lorem ipsum dolor sit amet, consectetur adipiscing elit, sed do eiusmod tempor incididunt ut labore et dolore magna aliqua. Ut enim ad minim veniam,</p>
    </article>
    <article class="post">
      <svg class="post-thumb" viewBox="0 0 314 164" role="img" aria-label="Photo of a team working at a glass board"><rect width="314" height="164" fill="#c8cdd1"/></svg>
      <h3>Nemo enim ipsam voluptatem quia</h3>
      <div class="post-meta"><span><svg width="11" height="11" viewBox="0 0 12 12"><rect x="1" y="2" width="10" height="9" fill="none" stroke="#555" stroke-width="1.5"/><path d="M1 5h10" stroke="#555"/></svg>March 25, 2017</span><span><svg width="12" height="11" viewBox="0 0 12 11"><path d="M1 1h10v7H5l-3 2V8H1z" fill="none" stroke="#555" stroke-width="1.2"/></svg>No comments</span></div>
      <p>Lorem ipsum dolor sit amet, consectetur adipiscing elit, sed do eiusmod tempor incididunt ut labore et dolore magna aliqua. Ut enim ad minim veniam,</p>
    </article>
    <article class="post">
      <svg class="post-thumb" viewBox="0 0 314 164" role="img" aria-label="Photo of a consultant standing in an open plan office"><rect width="314" height="164" fill="#8d7f72"/></svg>
      <h3>Nemo enim ipsam voluptatem quia</h3>
      <div class="post-meta"><span><svg width="11" height="11" viewBox="0 0 12 12"><rect x="1" y="2" width="10" height="9" fill="none" stroke="#555" stroke-width="1.5"/><path d="M1 5h10" stroke="#555"/></svg>March 25, 2017</span><span><svg width="12" height="11" viewBox="0 0 12 11"><path d="M1 1h10v7H5l-3 2V8H1z" fill="none" stroke="#555" stroke-width="1.2"/></svg>No comments</span></div>
      <p>Lorem ipsum dolor sit amet, consectetur adipiscing elit, sed do eiusmod tempor incididunt ut labore et dolore magna aliqua. Ut enim ad minim veniam,</p>
    </article>
  </div>
</section>

<section class="testimonial">
  <div class="avatar" role="img" aria-label="Portrait photo of the quoted client"></div>
  <p class="quote">“ Sed ut perspiciatis unde omnis iste natus error sit voluptatem accusantium doloremque laudantium, totam rem aperiam, eaque ipsa quae ab illo inventore veritatis et quasi architecto beatae vitae dicta sunt explicabo. Nemo enim ipsam voluptatem quia voluptas sit aspernatur aut odit aut fugit, sed quia consequuntur</p>
  <p class="quote-author">Daniel Hartwell, Brightmoor Counsel</p>
  <div class="quote-bars"><i class="on"></i><i></i><i></i></div>
</section>

<footer class="site-footer">
  <div class="footer-col contact-col">
    <h4>Contact Us</h4>
    <div class="contact-row"><svg width="16" height="20" viewBox="0 0 16 20"><path d="M8 1a6 6 0 0 0-6 6c0 5 6 12 6 12s6-7 6-12a6 6 0 0 0-6-6z" fill="none" stroke="#ddd" stroke-width="1.6"/><circle cx="8" cy="7" r="2" fill="#ddd"/></svg><span>Unit 4 Harlow Court,<br>Eastfield, Northbridge, Beds,</span></div>
    <div class="contact-row"><svg width="16" height="16" viewBox="0 0 24 24"><path fill="none" stroke="#ddd" stroke-width="1.8" d="M6.6 10.8a15 15 0 0 0 6.6 6.6l2.2-2.2c.3-.3.7-.4 1-.2 1.1.4 2.3.6 3.6.6.6 0 1 .4 1 1V20c0 .6-.4 1-1 1A17 17 0 0 1 3 4c0-.6.4-1 1-1h3.5c.6 0 1 .4 1 1 0 1.3.2 2.5.6 3.6.1.3 0 .7-.2 1z"/></svg><span>Phone : +44(0)20 7946 0321</span></div>
    <div class="contact-row"><svg width="16" height="14" viewBox="0 0 16 14"><rect x="1" y="2" width="14" height="10" fill="none" stroke="#ddd" stroke-width="1.5"/><path d="M1 2l7 6 7-6" fill="none" stroke="#ddd" stroke-width="1.5"/></svg><span>admin@brightmoor-counsel.com</span></div>
  </div>
  <div class="footer-col signup-col">
    <h4>Sign up to receive email</h4>
    <p>Excepteur sint occaecat cupidatat non proident, sunt in culpa qui Nemo enim ipsam voluptatem</p>
    <div class="field">Enter Name</div>
    <a class="btn-brand" href="#">Subscribe</a>
  </div>
  <div class="footer-col links-col">
    <h4>Quick Links</h4>
    <ul><li>Home</li><li>About Us</li><li>What we do</li><li>How we do it</li><li>Who are we</li><li>Contact Us</li></ul>
  </div>
  <div class="footer-col social-col">
    <h4>Social</h4>
    <ul><li><i></i>Neighborly</li><li><i></i>Chirpline</li><li><i></i>Orbitly</li><li><i></i>Streamview</li></ul>
  </div>
  <p class="copyright">Copyright © Brightmoor Counsel 2017. All rights reserved.</p>
</footer>

</body>
</html>
```